Commercial Refrigeration Service Company requires stylish and fresh looking flyer.

We need a flyer to hand out to new customers. It should have a photo and our branding, list all the services that are offered and our contact details.
We would like two flyers to be supplied, both identical though one offering a discount until July ( Half Price Service Fee ). The flyer should be clear, interesting and in similar colours to the branding package supplied.
Please look at our website for information about the services on offer:
www.brisko-coolworks.com.au

Target Market(s)

Cafes, bars, restaurants, pubs ect.

Font styles to use
Other font styles liked:
• Font package provided

Colors
85cae6
ffffff
333333

Requirements
Must have
• - The photo provided.
• - The company logo.
• - Similar feel to the website & business card.
• - Smooth layout and clear to understand.
Should not have
• - No clunky badges or prints.

```html
<!DOCTYPE html>
<html lang="en">
<head>
<meta charset="utf-8">
<title>Brisko Commercial Refrigeration Flyer</title>
<link rel="stylesheet" href="https://fonts.googleapis.com/css2?family=Josefin+Sans:wght@300;400;600&display=swap">
<style>
  :root {
    --brand-blue: #85cae6;
    --accent-blue: #5ec4ee;
    --charcoal: #333333;
    --white: #ffffff;
    --backdrop: #e4e4e4;
  }
  * { box-sizing: border-box; margin: 0; padding: 0; }
  html, body { width: 1200px; height: 1044px; overflow: hidden; background: var(--backdrop); }
  body { font-family: "Josefin Sans", sans-serif; position: relative; }

  .flyer { position: absolute; left: 30px; width: 1140px; box-shadow: 0 6px 18px rgba(0,0,0,.25); overflow: hidden; }

  /* Front */
  .flyer-front { top: 18px; height: 492px; background: var(--charcoal); }
  .hero-photo {
    position: absolute; left: 0; top: 0; width: 100%; height: 440px;
    background: linear-gradient(180deg, #6fb0e0 0%, #a9cde6 32%, #7f98a8 55%, #5b6470 75%, #8a8a86 100%);
  }
  .offer-badge {
    position: absolute; left: 26px; top: 10px; width: 196px; height: 196px;
    border-radius: 50%; background: var(--charcoal);
    box-shadow: 0 0 0 5px rgba(255,255,255,.85), 0 0 0 7px var(--charcoal);
    display: flex; flex-direction: column; align-items: center; justify-content: center;
    transform: rotate(-18deg); text-align: center; line-height: 1.05;
  }
  .offer-badge .offer-lead { color: var(--white); font-size: 23px; font-weight: 400; }
  .offer-badge .offer-term { color: var(--accent-blue); font-size: 23px; font-weight: 400; }
  .service-strip {
    position: absolute; left: 0; bottom: 0; width: 100%; height: 52px; padding: 4px 20px 0;
    display: flex; align-items: center; justify-content: center;
    color: var(--accent-blue); font-size: 24px; font-weight: 400; letter-spacing: 0; white-space: nowrap;
  }

  /* Back */
  .flyer-back { top: 530px; height: 496px; background: var(--charcoal); }
  .service-list { position: absolute; left: 74px; top: 20px; width: 540px; }
  .service-item { display: flex; gap: 22px; margin-bottom: 16px; }
  .service-icon { width: 36px; height: 46px; flex: none; margin-top: 2px; }
  .service-title { color: var(--accent-blue); font-size: 22px; font-weight: 400; margin-bottom: 4px; }
  .service-text { color: var(--white); font-size: 19px; font-weight: 300; line-height: 1.35; }
  .contact-email { position: absolute; left: 60px; top: 406px; color: var(--accent-blue); font-size: 24px; font-weight: 300; }
  .divider { position: absolute; left: 640px; top: 30px; width: 1px; height: 400px; background: var(--white); opacity: .8; }

  .brand-panel { position: absolute; left: 660px; top: 0; width: 480px; height: 440px; text-align: center; }
  .brand-name { margin-top: 90px; color: var(--white); font-size: 58px; font-weight: 400; letter-spacing: 30px; padding-left: 30px; }
  .brand-dot { width: 12px; height: 12px; border-radius: 50%; background: var(--white); margin: 26px auto 0; }
  .brand-tagline { margin-top: 36px; color: var(--accent-blue); font-size: 31px; font-weight: 400; letter-spacing: 3px; line-height: 1.35; }
  .accreditation { position: absolute; right: 60px; top: 318px; width: 104px; height: 44px; border-radius: 4px; background: rgba(255,255,255,.85); }
  .website { position: absolute; right: 36px; top: 396px; color: var(--accent-blue); font-size: 24px; font-weight: 300; }

  .call-band {
    position: absolute; left: 0; bottom: 0; width: 100%; height: 60px; background: var(--accent-blue);
    display: flex; align-items: center; justify-content: center;
    color: var(--charcoal); font-size: 28px; font-weight: 400; letter-spacing: 1px;
  }
</style>
</head>
<body>

<section class="flyer flyer-front">
  <div class="hero-photo" role="img" aria-label="Photo of the technician standing beside the branded service ute at the beach"></div>
  <div class="offer-badge">
    <span class="offer-lead">HALF PRICE</span>
    <span class="offer-lead">SERVICE FEE</span>
    <span class="offer-term">DISCOUNTED</span>
    <span class="offer-term">UNTIL JUNE</span>
    <span class="offer-term">2018</span>
  </div>
  <div class="service-strip">COMMERCIAL REFRIGERATION &amp; ELECTRICAL SERVICES, ICE MAKERS &amp; BEER SYSTEMS</div>
</section>

<section class="flyer flyer-back">
  <div class="service-list">
    <div class="service-item">
      <svg class="service-icon" viewBox="0 0 36 46" fill="none" stroke="#fff" stroke-width="2">
        <rect x="10" y="2" width="9" height="30" rx="4.5"/><circle cx="14.5" cy="36" r="7"/>
        <line x1="22" y1="8" x2="28" y2="8"/><line x1="22" y1="13" x2="28" y2="13"/><line x1="22" y1="18" x2="28" y2="18"/>
      </svg>
      <div>
        <h2 class="service-title">COMMERCIAL REFRIGERATION</h2>
        <p class="service-text">Cool rooms, freezer rooms, underbar &amp; upright<br>fridges/freezers, display fridges.</p>
      </div>
    </div>
    <div class="service-item">
      <svg class="service-icon" viewBox="0 0 36 46" fill="none" stroke="#fff" stroke-width="2">
        <path d="M4 6 L32 6 L28 42 L8 42 Z"/><rect x="10" y="16" width="8" height="8"/><rect x="18" y="24" width="8" height="8"/><rect x="11" y="30" width="7" height="7"/>
      </svg>
      <div>
        <h2 class="service-title">ICE MAKERS</h2>
        <p class="service-text">Cubers and flakers of all major brands.<br>Under counter to larger commercial systems.</p>
      </div>
    </div>
    <div class="service-item">
      <svg class="service-icon" viewBox="0 0 36 46" fill="none" stroke="#fff" stroke-width="2">
        <line x1="30" y1="2" x2="16" y2="20"/><path d="M4 20 H24 V28 H14 V34 H8 V28 H4 Z"/><circle cx="11" cy="40" r="2.5"/>
      </svg>
      <div>
        <h2 class="service-title">BEER SYSTEMS</h2>
        <p class="service-text">Single-Tap bar systems to Keg Room fit-outs.<br>Glycol systems, beer plumbing, CO² monitors.</p>
      </div>
    </div>
    <div class="service-item">
      <svg class="service-icon" viewBox="0 0 36 46" fill="none" stroke="#fff" stroke-width="2" stroke-linejoin="round">
        <path d="M22 2 L8 24 H18 L12 44 L30 18 H20 L28 2 Z"/>
      </svg>
      <div>
        <h2 class="service-title">ELECTRICAL</h2>
        <p class="service-text">LED lighting systems, power circuit repairs,<br>switchboards, air-curtains and outdoor<br>heating installations.</p>
      </div>
    </div>
  </div>
  <p class="contact-email">INFO@BRISKO-COOLWORKS.COM.AU</p>

  <div class="divider"></div>

  <div class="brand-panel">
    <h1 class="brand-name">BRISKO</h1>
    <div class="brand-dot"></div>
    <p class="brand-tagline">24HR SERVICE, SALES &amp;<br>INSTALLATIONS</p>
  </div>
  <div class="accreditation" role="img" aria-label="Trade accreditation badge"></div>
  <p class="website">WWW.BRISKO-COOLWORKS.COM.AU</p>

  <div class="call-band">CALL DEAN 0400 000 123</div>
</section>

</body>
</html>
```